Awesome photographers card for an awesome new business

Double sided business card Black background and silver logo in middle on one side. Details on otherside. please keep it simple

Industry/Entity Type

Photographer

Contact Information for Business Card

Gerald Fenwick
0452817360
GeraldFenwickPhotography47@mailbox.test
www.GeraldFenwickPhotography.test.au
Instagram _Gerald_fenwick

Requirements
Must have
• My logo in Silver
• please use instagram logo instead of "Instagram"

```html
<!DOCTYPE html>
<html lang="en">
<head>
<meta charset="utf-8">
<title>Gerald Fenwick – Business Card</title>
<link rel="stylesheet" href="https://fonts.googleapis.com/css2?family=Open+Sans:wght@400;600&display=swap">
<style>
  :root {
    --page-bg: #e9e7e4;
    --card-black: #111010;
    --text-white: #ffffff;
    --disc-grey: #4a4a4a;
    --disc-edge: #5c5c5c;
    --silver: #d4d4d4;
  }
  * { margin: 0; padding: 0; box-sizing: border-box; }
  html, body {
    width: 1200px;
    height: 900px;
    overflow: hidden;
    background: var(--page-bg);
    font-family: "Open Sans", Arial, sans-serif;
  }
  .business-card {
    position: absolute;
    left: 161px;
    top: 180px;
    width: 878px;
    height: 540px;
    background: var(--card-black);
    border-radius: 22px;
    color: var(--text-white);
    overflow: hidden;
  }
  .card-name {
    position: absolute;
    left: 50px;
    top: 64px;
    font-size: 30px;
    font-weight: 600;
    letter-spacing: 0.2px;
    text-transform: uppercase;
  }
  .brand-disc {
    position: absolute;
    left: 418px;
    top: 57px;
    width: 424px;
    height: 424px;
    border-radius: 50%;
    background: radial-gradient(circle at 45% 40%, #555 0%, var(--disc-grey) 60%, #3d3d3d 100%);
    border: 1px solid var(--disc-edge);
    display: flex;
    align-items: center;
    justify-content: center;
  }
  .brand-name {
    font-size: 30px;
    font-weight: 600;
    color: var(--silver);
    letter-spacing: 3px;
    text-transform: uppercase;
  }
  .contact-list {
    position: absolute;
    left: 50px;
    list-style: none;
    font-size: 21px;
    font-weight: 400;
  }
  .contact-list li {
    display: flex;
    align-items: center;
    gap: 7px;
    height: 31px;
  }
  .social-list { top: 326px; }
  .details-list { top: 400px; }
  .contact-icon { flex: none; fill: var(--text-white); }
  .social-square {
    width: 24px;
    height: 24px;
    background: var(--text-white);
    border-radius: 3px;
    margin-right: 4px;
  }
</style>
</head>
<body>
  <section class="business-card">
    <h1 class="card-name">Gerald Fenwick</h1>

    <div class="brand-disc">
      <span class="brand-name">Gerald Fenwick</span>
    </div>

    <ul class="contact-list social-list">
      <li><span class="social-square" aria-hidden="true"></span>Gerald_fenwick</li>
    </ul>

    <ul class="contact-list details-list">
      <li>
        <svg class="contact-icon" width="18" height="18" viewBox="0 0 24 24" aria-hidden="true">
          <path d="M6.6 10.8a15.1 15.1 0 0 0 6.6 6.6l2.2-2.2a1 1 0 0 1 1-.25 11.4 11.4 0 0 0 3.6.57 1 1 0 0 1 1 1V20a1 1 0 0 1-1 1A17 17 0 0 1 3 4a1 1 0 0 1 1-1h3.5a1 1 0 0 1 1 1c0 1.25.2 2.45.57 3.57a1 1 0 0 1-.25 1z"/>
        </svg>
        0452817360
      </li>
      <li>
        <svg class="contact-icon" width="18" height="18" viewBox="0 0 24 24" aria-hidden="true">
          <circle cx="12" cy="12" r="10"/>
          <path d="M2 12h20M12 2c3 3 3 17 0 20M12 2c-3 3-3 17 0 20" stroke="#111010" stroke-width="1.6" fill="none"/>
        </svg>
        www.GeraldFenwickPhotography.test.au
      </li>
      <li>
        <svg class="contact-icon" width="18" height="18" viewBox="0 0 24 24" aria-hidden="true">
          <rect x="2" y="5" width="20" height="14" rx="1.5"/>
          <path d="M2.5 6l9.5 7 9.5-7" stroke="#111010" stroke-width="1.6" fill="none"/>
        </svg>
        GeraldFenwickPhotography47@mailbox.test
      </li>
    </ul>
  </section>
</body>
</html>
```